Brisk Fixwell business card

I need business card for my business, I think you have all my details.six months ago I design with you car wrap design. We would like to design both side of the card. On front of card we would like logo , Name and our contact details.
At the back we are looking to mentioned our services.
The name will be:
Faridoullan Mestor
Managing Director
Ph:07952338417
Email:info@brisk-fixwell.com
Web:www.brisk-fixwell.com
So we have our logo, you don’t need to change the logo.
Please see the attachment.
Thanks

Target Market(s)

Home improvement

Industry/Entity Type

Home Improvement

Contact Information for Business Card

Company name: Brisk Fixwell
Name: Faridoullan Mestor
Position: Director
Ph:07952338417
Web: www.brisk-fixwell.com
Add: 42 Corvale Road
Hounslow
TW3 9KD
SECOND PERSON
Nizamuddel mestor
Position: Handyman
Ph: 07812 564037
Email: info@brisk-fixwell.com
Add: 18 Brackwin Lane Road
Hounslow
TW6 2LB

```html
<!DOCTYPE html>
<html lang="en">
<head>
<meta charset="utf-8">
<title>Brisk Fixwell business card</title>
<link href="https://fonts.googleapis.com/css2?family=Arimo:wght@400;700&display=swap" rel="stylesheet">
<style>
  :root {
    --brand-blue: #243a8c;
    --brand-blue-light: #2f4cb8;
    --brand-blue-dark: #1b2c6e;
    --accent-red: #e21d2c;
    --text-grey: #3d3d3d;
    --rule-grey: #b9b9b9;
    --card-white: #ffffff;
    --backdrop: #2b2b2b;
  }
  * { box-sizing: border-box; margin: 0; padding: 0; }
  html, body {
    width: 1200px; height: 1015px; overflow: hidden;
    background: var(--backdrop);
    font-family: "Arimo", Arial, sans-serif;
  }
  .canvas {
    position: relative; width: 1200px; height: 1015px;
  }
  .card {
    position: absolute; left: 190px; width: 820px; height: 469px;
    overflow: hidden; box-shadow: 0 10px 24px rgba(0,0,0,0.45);
  }
  /* back side */
  .card--back { top: 20px; }
  .back-pattern {
    position: absolute; inset: 0;
    background: linear-gradient(135deg, var(--brand-blue-light) 0%, var(--brand-blue) 50%, var(--brand-blue-dark) 100%);
  }
  .back-wordmark {
    position: absolute; right: 150px; top: 200px;
    display: flex; align-items: center; gap: 14px;
    color: var(--card-white); font-weight: 700; font-size: 40px; letter-spacing: 0.5px;
  }
  .mark-square { width: 26px; height: 26px; background: var(--card-white); }
  /* front side */
  .card--front { top: 526px; background: var(--card-white); }
  .front-wordmark {
    position: absolute; left: 58px; top: 150px;
    display: flex; align-items: center; gap: 14px;
    color: var(--brand-blue); font-weight: 700; font-size: 44px;
  }
  .front-wordmark .mark-square { background: var(--accent-red); width: 30px; height: 30px; }
  .divider {
    position: absolute; left: 452px; top: 40px; width: 1px; height: 270px;
    background: var(--rule-grey);
  }
  .contact {
    position: absolute; left: 488px; top: 46px; color: var(--text-grey);
  }
  .contact__name { color: var(--brand-blue); font-weight: 700; font-size: 23px; letter-spacing: 0.3px; }
  .contact__role { font-size: 18px; margin-top: 3px; letter-spacing: 0.5px; }
  .contact__list { list-style: none; margin-top: 18px; }
  .contact__list li { display: flex; align-items: center; gap: 10px; font-size: 18px; line-height: 30px; }
  .contact__list svg { width: 18px; height: 18px; fill: var(--brand-blue); flex: none; }
  .contact__web span { color: var(--brand-blue); }
  .contact__address { font-size: 18px; line-height: 26px; margin-top: 14px; margin-left: 28px; }
  .services {
    position: absolute; left: 0; bottom: 0; width: 100%; height: 132px;
    background: var(--brand-blue);
    display: flex; gap: 26px; padding: 30px 0 0 38px;
  }
  .services__col { list-style: none; color: var(--card-white); font-size: 21px; line-height: 34px; }
  .services__col.bulleted li::before {
    content: ""; display: inline-block; width: 8px; height: 8px; border-radius: 50%;
    background: var(--accent-red); margin-right: 8px; vertical-align: middle;
  }
</style>
</head>
<body>
<div class="canvas">
  <section class="card card--back" aria-label="Card back">
    <div class="back-pattern" role="img" aria-label="Repeating embossed brand emblem pattern on deep blue"></div>
    <div class="back-wordmark"><span>Brisk Fixwell</span><span class="mark-square"></span></div>
  </section>

  <section class="card card--front" aria-label="Card front">
    <div class="front-wordmark"><span>Brisk Fixwell</span><span class="mark-square"></span></div>
    <div class="divider"></div>
    <div class="contact">
      <div class="contact__name">FARIDOULLAN MESTOR</div>
      <div class="contact__role">DIRECTOR</div>
      <ul class="contact__list">
        <li><svg viewBox="0 0 24 24"><path d="M6.6 10.8a15.1 15.1 0 0 0 6.6 6.6l2.2-2.2a1 1 0 0 1 1-.25 11.4 11.4 0 0 0 3.6.57 1 1 0 0 1 1 1V20a1 1 0 0 1-1 1A17 17 0 0 1 3 4a1 1 0 0 1 1-1h3.5a1 1 0 0 1 1 1c0 1.25.2 2.45.57 3.57a1 1 0 0 1-.25 1z"/></svg>07952338417</li>
        <li><svg viewBox="0 0 24 24"><path d="M2 5h20v14H2z M2 5l10 8 10-8" fill="none" stroke="#243a8c" stroke-width="2"/></svg>info@brisk-fixwell.com</li>
        <li class="contact__web"><svg viewBox="0 0 24 24"><circle cx="12" cy="12" r="9" fill="none" stroke="#243a8c" stroke-width="2"/><path d="M3 12h18M12 3c3 3 3 15 0 18M12 3c-3 3-3 15 0 18" fill="none" stroke="#243a8c" stroke-width="1.6"/></svg>www.<span>brisk-fixwell</span>.com</li>
      </ul>
      <div class="contact__address">42 Corvale Road<br>Hounslow, TW3 9KD</div>
    </div>
    <div class="services">
      <ul class="services__col"><li>Plumbing</li><li>Carpentry</li></ul>
      <ul class="services__col bulleted"><li>Decking</li><li>Fence</li></ul>
      <ul class="services__col bulleted"><li>Gutter</li><li>Flooring</li></ul>
      <ul class="services__col bulleted"><li>Plastering</li><li>Tilling</li></ul>
      <ul class="services__col bulleted"><li>Painting &amp; Decorating</li><li>Gardening</li></ul>
    </div>
  </section>
</div>
</body>
</html>
```